Civil Engineering Business Card Design

We need a business card design for an Civil Engineering Company located in Naples, Florida. The company name is Durvel Engineering.
What we do:
Site Evaluation
Review existing site conditions and zoning
Evaluation of potential development options
Evaluation of environmental permitting challenges
Prepare alternative master site development or redevelopment plan
Calculate cost and time lines for site development
Address political, environmental, social, and economic impacts of site development
Site Design
Prepare master site development plans
Zoning, rezoning, and zoning amendments for land use changes
Evaluate zoning and environmental permitting challenges
Value engineer alternative land development design and products
Residential Development
Plat development and design
Homeowner association document development
Single family development ranging from affordable housing to large estate projects
Multi family development ranging from duplexes to large scale condominiums
Amenity facilities such as golf courses, parks and clubhouse sites
Commercial Development
Office site and park designs development plans
Industrial site and park development plans
Shopping center site development design
Hospital site design development
Institutional Development
School design development and redevelopment plans
Park design development and enhancement plans
Downtown redevelopment plans for new and existing structures
Theater and park plan development
Parking garage design development
Governmental administration building design
Design Services
Site development
Environmental assessment
Roadway alignment and development
Surface water management
Drainage design
Water distribution system
Fire service analysis
Sewage collection systems
Sewage pump station and force main design
Cable utility conduit layout
Construction details
Construction documents
Technical specifications
Alternative methods and materials analysis
Services During Construction
Development of bid documents
Solicitation and processing of bids
Cost review and analysis
Construction cost estimating
Onsite construction observation
Coordination of field modifications to address unforeseen site conditions
Assess value engineering design and contract work
Review of pay requests and shop drawings
Review of warranties
Development assessment of onsite and offsite mitigation
Verification of construction completion, close out, and certification
Processing final pay requests and turn over
We want a clean design on a white background. We have a current logo but are not happy with it so changes would be greatly appreciated.
Industry/Entity Type
Construction
Contact Information for Business Card
Durvel Engineering
Creative Engineering Solutions Through Integrity and Experience
Marcus Pellow, President
4870 Brisket Ridge Road
Suite 517C
Naples, FL 34987
239-555-0164-Office, 239-555-0192-Mobile
Marcus@DurvelEng.example, www.DurvelEng.example

```html
<!DOCTYPE html>
<html lang="en">
<head>
<meta charset="utf-8">
<title>Durvel Engineering – Business Card</title>
<link rel="stylesheet" href="https://fonts.googleapis.com/css2?family=Open+Sans:wght@400;600;700&display=swap">
<style>
  :root {
    --backdrop: #e4e4e6;
    --card: #ffffff;
    --ink: #3a3a3c;
    --ink-soft: #555558;
    --brand-blue: #3f7fc4;
    --band-blue: #4f86d6;
    --band-light: #8fb4ea;
    --line-dark: #2e2e30;
    --line-grey: #a9a9ad;
  }
  * { box-sizing: border-box; margin: 0; padding: 0; }
  html, body {
    width: 1200px;
    height: 900px;
    overflow: hidden;
    background: var(--backdrop);
    font-family: "Open Sans", Arial, sans-serif;
  }
  .card {
    position: absolute;
    left: 250px;
    width: 700px;
    height: 400px;
    background: var(--card);
    box-shadow: 0 8px 24px rgba(0, 0, 0, 0.12);
    overflow: hidden;
  }
  .card-back { top: 30px; }
  .card-front { top: 470px; }

  /* back side */
  .back-brand {
    position: absolute;
    inset: 0;
    display: flex;
    flex-direction: column;
    align-items: center;
    justify-content: center;
    gap: 14px;
  }
  .back-square {
    width: 70px;
    height: 70px;
    background: var(--brand-blue);
  }
  .back-name {
    font-size: 30px;
    font-weight: 700;
    letter-spacing: 1px;
    text-transform: uppercase;
    color: var(--ink);
  }

  /* front side */
  .swoosh {
    position: absolute;
    inset: 0;
    width: 100%;
    height: 100%;
  }
  .brand {
    position: absolute;
    left: 44px;
    top: 146px;
    display: flex;
    align-items: center;
    gap: 12px;
  }
  .brand-square {
    width: 42px;
    height: 42px;
    background: var(--brand-blue);
  }
  .brand-name {
    font-size: 27px;
    font-weight: 700;
    letter-spacing: 0.5px;
    text-transform: uppercase;
    color: var(--ink);
  }
  .person {
    position: absolute;
    right: 44px;
    top: 46px;
    text-align: right;
  }
  .person-name {
    font-size: 24px;
    font-weight: 600;
    color: var(--brand-blue);
    line-height: 1.15;
  }
  .person-title {
    font-size: 15px;
    color: var(--ink-soft);
  }
  .address {
    position: absolute;
    right: 44px;
    top: 196px;
    text-align: right;
    font-style: normal;
    font-size: 14px;
    line-height: 1.45;
    color: var(--ink-soft);
  }
  .contacts {
    position: absolute;
    left: 44px;
    top: 262px;
    list-style: none;
    font-size: 15px;
    line-height: 1.45;
    color: var(--ink-soft);
  }
  .contacts li {
    display: flex;
    align-items: center;
    gap: 8px;
  }
  .contact-icon {
    width: 12px;
    height: 12px;
    fill: var(--brand-blue);
    flex: none;
  }
</style>
</head>
<body>
  <section class="card card-back">
    <div class="back-brand">
      <div class="back-square"></div>
      <span class="back-name">Durvel Engineering</span>
    </div>
  </section>

  <section class="card card-front">
    <svg class="swoosh" viewBox="0 0 1000 572" preserveAspectRatio="none" aria-hidden="true">
      <defs>
        <linearGradient id="bandFill" x1="0" y1="0" x2="1" y2="0">
          <stop offset="0" stop-color="var(--band-blue)"/>
          <stop offset="0.55" stop-color="var(--band-light)"/>
          <stop offset="1" stop-color="var(--band-blue)"/>
        </linearGradient>
        <linearGradient id="lineFill" x1="0" y1="0" x2="1" y2="0">
          <stop offset="0" stop-color="var(--line-grey)" stop-opacity="0.2"/>
          <stop offset="0.5" stop-color="var(--line-grey)"/>
          <stop offset="1" stop-color="var(--line-dark)"/>
        </linearGradient>
      </defs>
      <path d="M0,522 C330,512 640,430 1000,392 L1000,572 L0,572 Z" fill="url(#bandFill)"/>
      <path d="M0,508 C330,498 640,412 1000,372" fill="none" stroke="url(#lineFill)" stroke-width="5"/>
    </svg>

    <div class="brand">
      <div class="brand-square"></div>
      <span class="brand-name">Durvel Engineering</span>
    </div>

    <div class="person">
      <p class="person-name">Marcus Pellow</p>
      <p class="person-title">President</p>
    </div>

    <address class="address">
      <p>4870 Brisket Ridge Road, Suite 517C</p>
      <p>Naples, FL 34987</p>
    </address>

    <ul class="contacts">
      <li>
        <svg class="contact-icon" viewBox="0 0 16 16" aria-hidden="true"><path d="M3.5 1 L6 1 L7 4.5 L5.3 5.8 C6.2 7.8 8.2 9.8 10.2 10.7 L11.5 9 L15 10 L15 12.5 C15 13.9 13.9 15 12.5 15 C6.7 15 1 9.3 1 3.5 C1 2.1 2.1 1 3.5 1 Z"/></svg>
        <span>239-555-0164</span>
      </li>
      <li>
        <svg class="contact-icon" viewBox="0 0 16 16" aria-hidden="true"><path d="M4.5 0 H11.5 A1.5 1.5 0 0 1 13 1.5 V14.5 A1.5 1.5 0 0 1 11.5 16 H4.5 A1.5 1.5 0 0 1 3 14.5 V1.5 A1.5 1.5 0 0 1 4.5 0 Z M5 2 V12 H11 V2 Z M8 13 A1 1 0 1 0 8 15 A1 1 0 1 0 8 13 Z"/></svg>
        <span>239-555-0192</span>
      </li>
      <li>
        <svg class="contact-icon" viewBox="0 0 16 16" aria-hidden="true"><path d="M1 3 H15 V4 L8 9 L1 4 Z M1 5.5 L8 10.5 L15 5.5 V13 H1 Z"/></svg>
        <span>Marcus@DurvelEng.example</span>
      </li>
    </ul>
  </section>
</body>
</html>
```